Freelance Translator in Need of a Business Card

I am a freelance Japanese to English translator. I work in the video game localization industry and do literary translation in my spare time. I would like to have both the English word 'Translator' and the Japanese '翻訳者' in the job title. The final design should evoke trust, openness, and reliability.

Target Market(s)

Video game localization companies
Japanese comic book artists

Industry/Entity Type

Business

Contact Information for Business Card

Daniel Forsvik, Translator
dan.forsvik@quellmail.net
torvenwords.com
twitter: @torven_wd

Colors

Designer to choose colors to be used in the design.

```html
<!DOCTYPE html>
<html lang="en">
<head>
<meta charset="utf-8">
<title>Torven Words — Business Card</title>
<link rel="stylesheet" href="https://fonts.googleapis.com/css2?family=Playfair+Display:wght@400;700&family=Noto+Serif+JP:wght@400&display=swap">
<style>
  :root {
    --page: #e9e6e1;
    --paper: #ffffff;
    --ink: #151515;
    --band-dark: #4a2326;
    --band-mid: #7a1f26;
    --band-bright: #d4293a;
    --rule: #d9d9d9;
    --divider: #7d7d7d;
    --accent: #9b1f2a;
    --back-black: #121212;
    --back-white: #f1f1f1;
  }
  * { box-sizing: border-box; margin: 0; padding: 0; }
  html, body { width: 1200px; height: 892px; overflow: hidden; }
  body {
    background: var(--page);
    font-family: "Playfair Display", Georgia, serif;
    color: var(--ink);
    position: relative;
  }
  .card {
    position: absolute;
    left: 250px;
    width: 700px;
    height: 400px;
    box-shadow: 0 6px 18px rgba(0,0,0,0.18);
    overflow: hidden;
  }
  .card-front { top: 31px; background: var(--paper); }
  .card-back { top: 461px; background: var(--back-black); }

  .front-title {
    position: absolute;
    top: 88px; left: 0; right: 0;
    text-align: center;
    font-weight: 700;
    font-size: 52px;
    letter-spacing: 0.5px;
  }
  .front-band {
    position: absolute;
    top: 190px; left: 0; right: 0;
    height: 72px;
    background: linear-gradient(90deg, var(--band-dark) 0%, var(--band-mid) 50%, var(--band-bright) 78%, var(--band-dark) 100%);
    border-top: 4px solid var(--rule);
    border-bottom: 4px solid var(--rule);
    display: flex;
    align-items: center;
    justify-content: center;
    gap: 22px;
    color: #fff;
  }
  .band-name { font-size: 27px; }
  .band-sep { width: 3px; height: 38px; background: #fff; }
  .band-role { font-size: 21px; }
  .band-role .jp { font-family: "Noto Serif JP", serif; margin-left: 6px; }

  .contact {
    position: absolute;
    top: 296px; left: 0; right: 0;
    display: flex;
    justify-content: center;
    align-items: center;
    gap: 28px;
    font-size: 17px;
    color: #333;
  }
  .contact-social { display: flex; align-items: center; gap: 10px; }
  .contact-divider { width: 2px; height: 66px; background: var(--divider); }
  .contact-list { list-style: none; display: flex; flex-direction: column; gap: 8px; }
  .contact-list li { display: flex; align-items: center; gap: 10px; }
  .dot { width: 12px; height: 12px; border-radius: 50%; background: var(--accent); flex: none; }
  .icon { width: 16px; height: 16px; flex: none; }

  .back-band {
    position: absolute;
    top: 110px; left: 0; right: 0;
    height: 180px;
    background: var(--back-white);
    display: flex;
    align-items: center;
    justify-content: center;
  }
  .back-title {
    font-weight: 700;
    font-size: 50px;
    letter-spacing: 1px;
    color: var(--ink);
  }
</style>
</head>
<body>
  <section class="card card-front">
    <h1 class="front-title">Torven Words</h1>
    <div class="front-band">
      <span class="band-name">Daniel Forsvik</span>
      <span class="band-sep"></span>
      <span class="band-role">Translator<span class="jp">翻訳者</span></span>
    </div>
    <div class="contact">
      <div class="contact-social">
        <span class="dot"></span>
        <span>@torven_wd</span>
      </div>
      <div class="contact-divider"></div>
      <ul class="contact-list">
        <li>
          <svg class="icon" viewBox="0 0 16 16" aria-hidden="true">
            <rect x="1" y="3" width="14" height="10" fill="var(--accent)"/>
            <path d="M1 3 L8 9 L15 3" fill="none" stroke="#fff" stroke-width="1.4"/>
          </svg>
          <span>dan.forsvik@quellmail.net</span>
        </li>
        <li>
          <svg class="icon" viewBox="0 0 16 16" aria-hidden="true">
            <circle cx="8" cy="8" r="7" fill="var(--accent)"/>
            <ellipse cx="8" cy="8" rx="3" ry="7" fill="none" stroke="#fff" stroke-width="1"/>
            <line x1="1" y1="8" x2="15" y2="8" stroke="#fff" stroke-width="1"/>
          </svg>
          <span>www.torvenwords.com</span>
        </li>
      </ul>
    </div>
  </section>

  <section class="card card-back">
    <div class="back-band">
      <h2 class="back-title">TORVEN WORDS</h2>
    </div>
  </section>
</body>
</html>
```